Local Roofing/Construction company business needs new biz card design

We need a new business card design, current cards are from the start of this operation and generic at best. We are a local Construction Company (General Contractor) with a majority of our work originating from insurance claims-exterior finish work is the main focus (Roofs-Siding-Gutters etc). Heavily involved with homeowners and the low ball offers they receive from insurance company's after a insurable event takes place. I have attached some of our original logo file(s) below.

```html
<!DOCTYPE html>
<html lang="en">
<head>
<meta charset="utf-8">
<title>Ironridge Construction – Business Card</title>
<link rel="stylesheet" href="https://fonts.googleapis.com/css2?family=Montserrat:wght@400;500;700;800&display=swap">
<style>
  :root {
    --bg: #2a2a2d;
    --card: #1e1e20;
    --card-edge: #2fd67a;
    --accent: #33d67d;
    --text: #f1f1f1;
    --muted: #d8d8d8;
    --pattern-light: #8a8a8a;
    --pattern-dark: #141415;
  }
  * { margin: 0; padding: 0; box-sizing: border-box; }
  html, body { width: 1200px; height: 900px; overflow: hidden; }
  body {
    background: var(--bg);
    font-family: "Montserrat", sans-serif;
    color: var(--text);
  }
  .canvas {
    position: relative;
    width: 1200px;
    height: 900px;
  }
  .card {
    position: absolute;
    left: 250px;
    width: 700px;
    height: 400px;
    border-radius: 22px;
    background: var(--card);
    border-bottom: 6px solid var(--card-edge);
    overflow: hidden;
    box-shadow: 0 18px 40px rgba(0,0,0,0.45);
  }
  .card--back { top: 40px; }
  .card--front { top: 470px; }

  /* Back side */
  .back-pattern {
    position: absolute;
    inset: 0;
    background: linear-gradient(120deg, var(--pattern-light) 0%, #4a4a4c 30%, #202022 60%, var(--pattern-dark) 100%);
    opacity: 0.9;
  }
  .back-mark {
    position: absolute;
    right: 90px;
    top: 70px;
    font-weight: 800;
    font-size: 30px;
    letter-spacing: 1px;
    color: var(--accent);
  }

  /* Front side */
  .brand {
    position: absolute;
    top: 34px;
    right: 40px;
    display: flex;
    align-items: center;
    gap: 14px;
  }
  .brand__square {
    width: 46px;
    height: 46px;
    border-radius: 6px;
    background: var(--accent);
  }
  .brand__name {
    font-weight: 800;
    font-size: 20px;
    line-height: 1.15;
    letter-spacing: 0.5px;
    color: var(--text);
    text-transform: uppercase;
  }
  .person {
    position: absolute;
    left: 44px;
    top: 208px;
  }
  .person__name {
    font-weight: 700;
    font-size: 30px;
    color: var(--accent);
    letter-spacing: 0.3px;
  }
  .person__role {
    font-size: 16px;
    font-weight: 500;
    color: var(--text);
    margin-top: 2px;
  }
  .divider {
    position: absolute;
    left: 44px;
    right: 40px;
    top: 292px;
    height: 1px;
    background: var(--accent);
  }
  .contacts {
    position: absolute;
    left: 44px;
    top: 306px;
    list-style: none;
    font-size: 15px;
    font-weight: 500;
    color: var(--muted);
  }
  .contacts li {
    display: flex;
    align-items: center;
    gap: 10px;
    height: 24px;
  }
  .contacts svg { width: 14px; height: 14px; fill: var(--accent); flex: none; }
  .address {
    position: absolute;
    right: 40px;
    top: 318px;
    text-align: right;
    font-size: 15px;
    font-weight: 500;
    line-height: 1.45;
    color: var(--muted);
  }
</style>
</head>
<body>
<main class="canvas">

  <section class="card card--back" aria-label="Card back">
    <div class="back-pattern" role="img" aria-label="Repeating monogram pattern in glossy black and silver tones"></div>
    <div class="back-mark">IRONRIDGE</div>
  </section>

  <section class="card card--front" aria-label="Card front">
    <div class="brand">
      <div class="brand__square"></div>
      <div class="brand__name">Ironridge<br>Construction</div>
    </div>

    <div class="person">
      <h1 class="person__name">Daniel Brooks</h1>
      <p class="person__role">Owner</p>
    </div>

    <div class="divider"></div>

    <ul class="contacts">
      <li>
        <svg viewBox="0 0 24 24" aria-hidden="true"><path d="M6.6 10.8a15.1 15.1 0 0 0 6.6 6.6l2.2-2.2a1 1 0 0 1 1-.25 11.4 11.4 0 0 0 3.6.57 1 1 0 0 1 1 1V20a1 1 0 0 1-1 1A17 17 0 0 1 3 4a1 1 0 0 1 1-1h3.5a1 1 0 0 1 1 1c0 1.25.2 2.45.57 3.57a1 1 0 0 1-.25 1z"/></svg>
        555-014-2270
      </li>
      <li>
        <svg viewBox="0 0 24 24" aria-hidden="true"><path d="M3 5h18a1 1 0 0 1 1 1v12a1 1 0 0 1-1 1H3a1 1 0 0 1-1-1V6a1 1 0 0 1 1-1zm9 7.5L4 7.4V8l8 5 8-5v-.6z"/></svg>
        info@ironridgebuild.com
      </li>
      <li>
        <svg viewBox="0 0 24 24" aria-hidden="true"><path d="M12 2a10 10 0 1 0 0 20 10 10 0 0 0 0-20zm6.9 9h-3a15.6 15.6 0 0 0-1.3-5.6A8 8 0 0 1 18.9 11zM12 4.1c.9 1.3 1.7 3.6 1.9 6.9h-3.8c.2-3.3 1-5.6 1.9-6.9zM9.4 5.4A15.6 15.6 0 0 0 8.1 11h-3a8 8 0 0 1 4.3-5.6zM5.1 13h3a15.6 15.6 0 0 0 1.3 5.6A8 8 0 0 1 5.1 13zm6.9 6.9c-.9-1.3-1.7-3.6-1.9-6.9h3.8c-.2 3.3-1 5.6-1.9 6.9zm2.6-1.3a15.6 15.6 0 0 0 1.3-5.6h3a8 8 0 0 1-4.3 5.6z"/></svg>
        www.ironridgebuild.com
      </li>
    </ul>

    <p class="address">48 Harlow Creek Rd<br>Fairview, MO 63000</p>
  </section>

</main>
</body>
</html>
```